Web Design Project

We have a website in beta that needs updating and are looking for a freash new look for the Home page including Logo.
Our company is called " Kip Dorra " we specialize in classified advertising using video. Our consumers will be businesses selling a product or service. Please visit www.kipdorra.com
Our aim past this point is to engage a developer to write the code based on the best design. Our target market is the U.S and I have included some of the landing pages to give you a better idea of what we are trying to acheive

http://www.kipdorra.com/
http://www.kipdorra.com/cars_home.php
http://www.kipdorra.com/boats.php
http://www.kipdorra.com/electronic.php
http://www.kipdorra.com/realestate.php
http://www.kipdorra.com/roommates.php
Updates

Target Market(s)

20-35 yr old people who are connected to the internet via mobile phone and use social media on a daily/weekly basis

Industry/Entity Type

Advertising

Requirements
Must have
• We would like to use lots of images to convey it is a video driven website business
Nice to have
• Logo to incorporate same theme of website ( ie ) you are here to watch videos of thinhs to buy & sell
Should not have
• This is to be a freash new site with large type and bold fonts

```html
<!DOCTYPE html>
<html lang="en">
<head>
<meta charset="utf-8">
<title>Kip Dorra – Home</title>
<link href="https://fonts.googleapis.com/css2?family=Roboto:wght@300;400;500;700;900&family=Roboto+Condensed:wght@400;700&display=swap" rel="stylesheet">
<style>
:root{
  --red:#d71f26;
  --ink:#2a2a2a;
  --ink-2:#383838;
  --page:#e7e7e7;
  --card:#ffffff;
  --muted:#8a8a8a;
  --yellow:#f6c500;
  --line:#cfcfcf;
}
*{box-sizing:border-box;margin:0;padding:0}
html,body{width:1200px;height:3300px;overflow:hidden}
body{background:var(--page);font-family:"Roboto",Arial,sans-serif;color:var(--ink)}
a{color:inherit;text-decoration:none}
.page{width:1200px;height:3300px;position:relative;overflow:hidden}

/* header */
.topbar{height:112px;background:var(--ink);position:relative}
.brand{position:absolute;left:32px;top:30px;display:flex;align-items:center;gap:10px;color:#fff;font-weight:700;font-size:30px}
.brand-dot{width:26px;height:26px;border-radius:50%;background:var(--red)}
.promo-tag{position:absolute;left:600px;top:40px;width:120px;height:44px;background:var(--red);border-radius:3px}
.top-links{position:absolute;right:30px;top:22px;text-align:right;color:#cfcfcf;font-size:14px}
.top-links .create{display:inline-block;margin-bottom:12px;color:#fff}
.top-links .create b{color:var(--red);margin-left:4px}
.top-links .login{margin-left:18px;color:#fff}
.account-links span{margin:0 6px}

.mainnav{height:48px;background:var(--ink-2);display:flex;align-items:center;padding-left:112px;position:relative}
.mainnav a{color:#e6e6e6;font-size:16px;font-weight:500;padding:0 22px;line-height:48px}
.mainnav a.active{background:var(--red);color:#fff}
.search{position:absolute;left:660px;top:8px;width:320px;height:32px;background:#2b2b2b;border:1px solid #555;color:#ddd;font-size:15px;padding:6px 12px}
.search svg{position:absolute;right:10px;top:8px}
.cart-btn{position:absolute;left:1000px;top:8px;width:32px;height:32px;background:var(--red);display:flex;align-items:center;justify-content:center}
.nav-drop{position:absolute;left:1044px;top:8px;width:32px;height:32px;background:#2b2b2b;border:1px solid #555}

/* hero */
.hero{height:540px;position:relative;background:linear-gradient(160deg,#5f8f8c 0%,#2f5c5f 45%,#1c3436 100%);overflow:hidden}
.hero-headline{position:absolute;right:110px;top:60px;text-align:right;font-weight:900;font-size:92px;line-height:88px;color:#1f2a2c;letter-spacing:-1px}
.hero-sub{position:absolute;right:250px;top:244px;font-family:"Roboto Condensed",Arial,sans-serif;font-size:17px;font-weight:700;color:var(--red);letter-spacing:1px}
.hero-cta{position:absolute;left:124px;top:440px;background:var(--red);color:#fff;font-size:17px;font-weight:500;padding:10px 30px}
.hero-tagline{position:absolute;right:110px;bottom:36px;display:flex;align-items:center;gap:20px;color:#fff;font-family:"Roboto Condensed",Arial,sans-serif;font-weight:700;font-size:28px}
.hero-tagline .sep{width:2px;height:36px;background:#fff}
.hero-tagline .partner{font-size:24px}

/* features */
.features{display:flex;justify-content:center;margin-top:30px}
.feature{width:220px;height:130px;display:flex;align-items:center;gap:16px;padding:0 18px;color:#fff}
.feature.red{background:var(--red)}
.feature.dark{background:var(--ink-2)}
.feature h3{font-size:17px;font-weight:700;margin-bottom:6px}
.feature p{font-size:12px;line-height:16px;color:#f2f2f2}

/* product sections */
.section{width:960px;margin:0 auto}
.section-head{display:flex;align-items:center;height:32px;position:relative}
.section-head::after{content:"";position:absolute;left:0;right:0;top:16px;height:1px;background:var(--line);z-index:0}
.section-title{position:relative;z-index:1;background:var(--red);color:#fff;font-size:16px;font-weight:500;padding:0 18px;line-height:32px}
.arrow-btn{position:relative;z-index:1;width:32px;height:32px;background:var(--ink-2);color:#fff;display:flex;align-items:center;justify-content:center;margin-left:2px}
.view-all{position:relative;z-index:1;background:var(--ink-2);color:#fff;font-size:16px;padding:0 18px;line-height:32px;margin-left:2px}
.product-grid{display:grid;grid-template-columns:repeat(4,225px);gap:16px 20px;margin-top:16px}
.product-card{background:var(--card);height:320px;padding:12px;text-align:center;position:relative}
.product-media{height:170px;position:relative;background:linear-gradient(135deg,var(--a),var(--b))}
.badge{position:absolute;right:-12px;top:-22px;width:44px;height:44px;border-radius:50%;background:var(--yellow);color:#fff;font-size:13px;font-weight:700;display:flex;align-items:center;justify-content:center}
.media-btn{position:absolute;bottom:0;width:28px;height:28px;background:var(--ink-2);color:#fff;font-size:18px;line-height:28px}
.media-btn.plus{left:0}
.media-btn.minus{right:0}
.stars{position:absolute;left:0;right:0;bottom:6px;color:var(--yellow);font-size:13px;letter-spacing:2px}
.product-text{font-size:13px;line-height:18px;color:var(--muted);margin:16px 14px 8px}
.price{font-size:22px;font-weight:700;color:var(--red);display:flex;justify-content:center;align-items:center;gap:12px}
.btn-more{display:inline-block;margin-top:12px;background:var(--ink-2);color:#fff;font-size:12px;padding:8px 20px}

/* partners */
.partners{height:210px;background:#fff;margin-top:8px;display:flex;align-items:center;justify-content:space-around;padding:0 150px}
.partner-name{font-size:26px;font-weight:500;color:#6f6f6f}

/* ad banner */
.ebook-banner{width:960px;height:120px;margin:60px auto 0;background:#fff;display:flex;align-items:center;border:1px solid #d5d5d5}
.ebook-art{width:220px;height:118px;background:linear-gradient(135deg,#f4d35a,#2f73b8)}
.ebook-copy{flex:1;background:#2e8bcf;height:118px;color:#fff;font-size:24px;line-height:30px;padding:28px 40px}
.ebook-publisher{width:200px;height:118px;background:#2e8bcf;color:#fff;font-size:22px;font-weight:500;display:flex;align-items:center;justify-content:center}

/* quote band */
.quote-band{position:absolute;left:0;top:3030px;width:1200px;height:70px;background:var(--red);color:#fff;font-size:15px;display:flex;align-items:center;justify-content:center}

/* footer */
.site-footer{position:absolute;left:0;top:3100px;width:1200px;height:160px;background:var(--ink);color:#bdbdbd;padding:22px 120px 0;display:grid;grid-template-columns:150px 170px 170px 210px 1fr;gap:10px}
.site-footer h4{color:#fff;font-size:13px;font-weight:700;margin-bottom:10px}
.site-footer li{list-style:none;font-size:12px;line-height:16px}
.footer-map{width:160px;height:100px;background:linear-gradient(180deg,#6a6a6a,#4f4f4f)}
.subscribe{display:flex;margin-bottom:12px}
.subscribe span{flex:1;height:28px;background:#fff;color:#999;font-size:11px;padding:7px 8px}
.subscribe b{width:60px;height:28px;background:var(--red)}
.pay-cards{display:flex;gap:6px;margin-bottom:12px}
.pay-cards span{width:40px;height:24px;background:#5a5a5a;border-radius:2px}
.socials{display:flex;gap:8px}
.socials span{width:26px;height:26px;border-radius:50%;background:#4e4e4e}
.bottom-bar{position:absolute;left:0;top:3260px;width:1200px;height:40px;background:#1e1e1e;color:#8f8f8f;font-size:12px;display:flex;align-items:center;padding-left:120px;gap:40px}
.bottom-bar nav span{margin-right:22px}
</style>
</head>
<body>
<div class="page">

<header>
  <div class="topbar">
    <a class="brand" href="http://www.kipdorra.com/"><span class="brand-dot"></span>Kip Dorra</a>
    <span class="promo-tag"></span>
    <div class="top-links">
      <span class="create">create an ad <b>▾</b></span><span class="login">Log in ▾</span>
      <div class="account-links"><span>welcome msg</span>|<span>my account</span>|<span>my wishlist</span>|<span>log in</span></div>
    </div>
  </div>
  <nav class="mainnav">
    <a class="active" href="http://www.kipdorra.com/">Home</a>
    <a href="http://www.kipdorra.com/boats.php">Boats</a>
    <a href="#">Buy</a>
    <a href="#">Sell</a>
    <a href="#">Promos</a>
    <a href="#">Contact</a>
    <div class="search">search for books
      <svg width="14" height="14" viewBox="0 0 14 14"><circle cx="6" cy="6" r="4.5" fill="none" stroke="#ddd" stroke-width="1.6"/><line x1="9.3" y1="9.3" x2="13" y2="13" stroke="#ddd" stroke-width="1.6"/></svg>
    </div>
    <span class="cart-btn"><svg width="18" height="16" viewBox="0 0 18 16"><path d="M1 1h3l2 9h9l2-7H5" fill="none" stroke="#fff" stroke-width="1.6"/><circle cx="7" cy="14" r="1.4" fill="#fff"/><circle cx="14" cy="14" r="1.4" fill="#fff"/></svg></span>
    <span class="nav-drop"></span>
  </nav>
</header>

<section class="hero" role="img" aria-label="Underwater scene with sunglasses sinking through teal water">
  <h1 class="hero-headline">REASON IS<br>EXPECTED</h1>
  <p class="hero-sub">KIRAN DAVOS + SERA ROLF</p>
  <a class="hero-cta" href="#">pre-order now</a>
  <div class="hero-tagline">BEYOND REASON<span class="sep"></span><span class="partner">Corvane</span></div>
</section>

<section class="features">
  <div class="feature red">
    <svg width="42" height="50" viewBox="0 0 42 50"><rect x="3" y="5" width="36" height="42" rx="3" fill="#fff"/><rect x="14" y="1" width="14" height="8" rx="2" fill="#fff" stroke="#d71f26" stroke-width="2"/><line x1="10" y1="20" x2="32" y2="20" stroke="#d71f26" stroke-width="3"/><line x1="10" y1="28" x2="32" y2="28" stroke="#d71f26" stroke-width="3"/><line x1="10" y1="36" x2="26" y2="36" stroke="#d71f26" stroke-width="3"/></svg>
    <div><h3>Perspiciatis</h3><p>Nemo nisi ipsum quas illo dolores ut voluptatem</p></div>
  </div>
  <div class="feature dark">
    <svg width="48" height="48" viewBox="0 0 48 48"><rect x="3" y="7" width="42" height="38" rx="3" fill="#fff"/><rect x="3" y="7" width="42" height="10" fill="#bbb"/><rect x="12" y="2" width="4" height="10" fill="#fff"/><rect x="32" y="2" width="4" height="10" fill="#fff"/><text x="24" y="39" font-family="Roboto,Arial,sans-serif" font-size="20" font-weight="700" fill="#383838" text-anchor="middle">23</text></svg>
    <div><h3>Perspiciatis</h3><p>Nemo nisi ipsum quas illo dolores ut voluptatem</p></div>
  </div>
  <div class="feature red">
    <svg width="40" height="52" viewBox="0 0 40 52"><circle cx="20" cy="19" r="16" fill="#fff"/><rect x="12" y="32" width="16" height="10" fill="#fff"/><rect x="14" y="44" width="12" height="5" rx="2" fill="#fff"/></svg>
    <div><h3>Perspiciatis</h3><p>Nemo nisi ipsum quas illo dolores ut voluptatem</p></div>
  </div>
</section>

<!-- new products -->
<section class="section" style="margin-top:80px">
  <div class="section-head"><span class="section-title">new products</span><span class="arrow-btn">‹</span><span class="arrow-btn">›</span></div>
  <div class="product-grid" style="margin-top:40px">
    <article class="product-card"><div class="product-media" style="--a:#c9b6a4;--b:#6b5b50" role="img" aria-label="Product photo of a person in a light interior"><span class="badge">new</span><span class="stars">★★★★★</span><span class="media-btn plus">+</span><span class="media-btn minus">−</span></div><p class="product-text">Nemo nisi ipsum quas illo dolores ut voluptatem</p><div class="price">$ 543.00 <svg width="20" height="18" viewBox="0 0 18 16"><path d="M1 1h3l2 9h9l2-7H5" fill="none" stroke="#d71f26" stroke-width="1.6"/><circle cx="7" cy="14" r="1.4" fill="#d71f26"/><circle cx="14" cy="14" r="1.4" fill="#d71f26"/></svg></div><a class="btn-more" href="#">read more</a></article>
    <article class="product-card"><div class="product-media" style="--a:#8c8c8c;--b:#3d3d3d" role="img" aria-label="Product photo of a person at a desk"><span class="stars">★★★★★</span><span class="media-btn plus">+</span><span class="media-btn minus">−</span></div><p class="product-text">Nemo nisi ipsum quas illo dolores ut voluptatem</p><div class="price">$ 543.00 <svg width="20" height="18" viewBox="0 0 18 16"><path d="M1 1h3l2 9h9l2-7H5" fill="none" stroke="#d71f26" stroke-width="1.6"/><circle cx="7" cy="14" r="1.4" fill="#d71f26"/><circle cx="14" cy="14" r="1.4" fill="#d71f26"/></svg></div><a class="btn-more" href="#">read more</a></article>
    <article class="product-card"><div class="product-media" style="--a:#d8c2ad;--b:#8a6d55" role="img" aria-label="Product photo of hands holding a device"><span class="badge">new</span><span class="stars">★★★★★</span><span class="media-btn plus">+</span><span class="media-btn minus">−</span></div><p class="product-text">Nemo nisi ipsum quas illo dolores ut voluptatem</p><div class="price">$ 543.00 <svg width="20" height="18" viewBox="0 0 18 16"><path d="M1 1h3l2 9h9l2-7H5" fill="none" stroke="#d71f26" stroke-width="1.6"/><circle cx="7" cy="14" r="1.4" fill="#d71f26"/><circle cx="14" cy="14" r="1.4" fill="#d71f26"/></svg></div><a class="btn-more" href="#">read more</a></article>
    <article class="product-card"><div class="product-media" style="--a:#e2e2e2;--b:#7d7d7d" role="img" aria-label="Product photo of a silver car"><span class="badge">new</span><span class="stars">★★★★★</span><span class="media-btn plus">+</span><span class="media-btn minus">−</span></div><p class="product-text">Nemo nisi ipsum quas illo dolores ut voluptatem</p><div class="price">$ 543.00 <svg width="20" height="18" viewBox="0 0 18 16"><path d="M1 1h3l2 9h9l2-7H5" fill="none" stroke="#d71f26" stroke-width="1.6"/><circle cx="7" cy="14" r="1.4" fill="#d71f26"/><circle cx="14" cy="14" r="1.4" fill="#d71f26"/></svg></div><a class="btn-more" href="#">read more</a></article>
  </div>
</section>

<!-- bestseller products -->
<section class="section" style="margin-top:60px">
  <div class="section-head"><span class="section-title">bestseller products</span><span class="arrow-btn">‹</span><span class="arrow-btn">›</span></div>
  <div class="product-grid">
    <article class="product-card"><div class="product-media" style="--a:#4a4a4a;--b:#1c1c1c" role="img" aria-label="Product photo of a dark evening outfit"><span class="stars">★★★★★</span><span class="media-btn plus">+</span><span class="media-btn minus">−</span></div><p class="product-text">Nemo nisi ipsum quas illo dolores ut voluptatem</p><div class="price">$ 543.00 <svg width="20" height="18" viewBox="0 0 18 16"><path d="M1 1h3l2 9h9l2-7H5" fill="none" stroke="#d71f26" stroke-width="1.6"/><circle cx="7" cy="14" r="1.4" fill="#d71f26"/><circle cx="14" cy="14" r="1.4" fill="#d71f26"/></svg></div><a class="btn-more" href="#">read more</a></article>
    <article class="product-card"><div class="product-media" style="--a:#7fb8d8;--b:#c9b27a" role="img" aria-label="Product photo of a tropical beach with huts"><span class="badge">20%</span><span class="stars">★★★★★</span><span class="media-btn plus">+</span><span class="media-btn minus">−</span></div><p class="product-text">Nemo nisi ipsum quas illo dolores ut voluptatem</p><div class="price">$ 543.00 <svg width="20" height="18" viewBox="0 0 18 16"><path d="M1 1h3l2 9h9l2-7H5" fill="none" stroke="#d71f26" stroke-width="1.6"/><circle cx="7" cy="14" r="1.4" fill="#d71f26"/><circle cx="14" cy="14" r="1.4" fill="#d71f26"/></svg></div><a class="btn-more" href="#">read more</a></article>
    <article class="product-card"><div class="product-media" style="--a:#3f6fa8;--b:#7a3d2a" role="img" aria-label="Product photo of a red house under a blue sky"><span class="badge">20%</span><span class="stars">★★★★★</span><span class="media-btn plus">+</span><span class="media-btn minus">−</span></div><p class="product-text">Nemo nisi ipsum quas illo dolores ut voluptatem</p><div class="price">$ 543.00 <svg width="20" height="18" viewBox="0 0 18 16"><path d="M1 1h3l2 9h9l2-7H5" fill="none" stroke="#d71f26" stroke-width="1.6"/><circle cx="7" cy="14" r="1.4" fill="#d71f26"/><circle cx="14" cy="14" r="1.4" fill="#d71f26"/></svg></div><a class="btn-more" href="#">read more</a></article>
    <article class="product-card"><div class="product-media" style="--a:#1f3f7a;--b:#5fa6c8" role="img" aria-label="Product photo of a villa with a pool at dusk"><span class="stars">★★★★★</span><span class="media-btn plus">+</span><span class="media-btn minus">−</span></div><p class="product-text">Nemo nisi ipsum quas illo dolores ut voluptatem</p><div class="price">$ 543.00 <svg width="20" height="18" viewBox="0 0 18 16"><path d="M1 1h3l2 9h9l2-7H5" fill="none" stroke="#d71f26" stroke-width="1.6"/><circle cx="7" cy="14" r="1.4" fill="#d71f26"/><circle cx="14" cy="14" r="1.4" fill="#d71f26"/></svg></div><a class="btn-more" href="#">read more</a></article>
  </div>
</section>

<!-- featured products -->
<section class="section" style="margin-top:60px">
  <div class="section-head"><span class="section-title">featured products</span><span class="view-all">view all</span></div>
  <div class="product-grid">
    <article class="product-card"><div class="product-media" style="--a:#d9d3c7;--b:#8e8576" role="img" aria-label="Product photo of a modern living room"><span class="stars">★★★★★</span><span class="media-btn plus">+</span><span class="media-btn minus">−</span></div><p class="product-text">Nemo nisi ipsum quas illo dolores ut voluptatem</p><div class="price">$ 543.00 <svg width="20" height="18" viewBox="0 0 18 16"><path d="M1 1h3l2 9h9l2-7H5" fill="none" stroke="#d71f26" stroke-width="1.6"/><circle cx="7" cy="14" r="1.4" fill="#d71f26"/><circle cx="14" cy="14" r="1.4" fill="#d71f26"/></svg></div><a class="btn-more" href="#">read more</a></article>
    <article class="product-card"><div class="product-media" style="--a:#9a8d80;--b:#4f4740" role="img" aria-label="Product photo of a young man"><span class="stars">★★★★★</span><span class="media-btn plus">+</span><span class="media-btn minus">−</span></div><p class="product-text">Nemo nisi ipsum quas illo dolores ut voluptatem</p><div class="price">$ 543.00 <svg width="20" height="18" viewBox="0 0 18 16"><path d="M1 1h3l2 9h9l2-7H5" fill="none" stroke="#d71f26" stroke-width="1.6"/><circle cx="7" cy="14" r="1.4" fill="#d71f26"/><circle cx="14" cy="14" r="1.4" fill="#d71f26"/></svg></div><a class="btn-more" href="#">read more</a></article>
    <article class="product-card"><div class="product-media" style="--a:#6a8fb3;--b:#2b3e57" role="img" aria-label="Product photo of a house at twilight"><span class="stars">★★★★★</span><span class="media-btn plus">+</span><span class="media-btn minus">−</span></div><p class="product-text">Nemo nisi ipsum quas illo dolores ut voluptatem</p><div class="price">$ 543.00 <svg width="20" height="18" viewBox="0 0 18 16"><path d="M1 1h3l2 9h9l2-7H5" fill="none" stroke="#d71f26" stroke-width="1.6"/><circle cx="7" cy="14" r="1.4" fill="#d71f26"/><circle cx="14" cy="14" r="1.4" fill="#d71f26"/></svg></div><a class="btn-more" href="#">read more</a></article>
    <article class="product-card"><div class="product-media" style="--a:#e0a070;--b:#a3402a" role="img" aria-label="Product photo of a plated meal"><span class="stars">★★★★★</span><span class="media-btn plus">+</span><span class="media-btn minus">−</span></div><p class="product-text">Nemo nisi ipsum quas illo dolores ut voluptatem</p><div class="price">$ 543.00 <svg width="20" height="18" viewBox="0 0 18 16"><path d="M1 1h3l2 9h9l2-7H5" fill="none" stroke="#d71f26" stroke-width="1.6"/><circle cx="7" cy="14" r="1.4" fill="#d71f26"/><circle cx="14" cy="14" r="1.4" fill="#d71f26"/></svg></div><a class="btn-more" href="#">read more</a></article>
    <article class="product-card"><div class="product-media" style="--a:#5a1f22;--b:#151515" role="img" aria-label="Product photo of red high heels"><span class="stars">★★★★★</span><span class="media-btn plus">+</span><span class="media-btn minus">−</span></div><p class="product-text">Nemo nisi ipsum quas illo dolores ut voluptatem</p><div class="price">$ 543.00 <svg width="20" height="18" viewBox="0 0 18 16"><path d="M1 1h3l2 9h9l2-7H5" fill="none" stroke="#d71f26" stroke-width="1.6"/><circle cx="7" cy="14" r="1.4" fill="#d71f26"/><circle cx="14" cy="14" r="1.4" fill="#d71f26"/></svg></div><a class="btn-more" href="#">read more</a></article>
    <article class="product-card"><div class="product-media" style="--a:#e6d7c4;--b:#a08a70" role="img" aria-label="Product photo of a person resting in bed"><span class="stars">★★★★★</span><span class="media-btn plus">+</span><span class="media-btn minus">−</span></div><p class="product-text">Nemo nisi ipsum quas illo dolores ut voluptatem</p><div class="price">$ 543.00 <svg width="20" height="18" viewBox="0 0 18 16"><path d="M1 1h3l2 9h9l2-7H5" fill="none" stroke="#d71f26" stroke-width="1.6"/><circle cx="7" cy="14" r="1.4" fill="#d71f26"/><circle cx="14" cy="14" r="1.4" fill="#d71f26"/></svg></div><a class="btn-more" href="#">read more</a></article>
    <article class="product-card"><div class="product-media" style="--a:#b8b8b8;--b:#5a5a5a" role="img" aria-label="Product photo of a quiet city street"><span class="stars">★★★★★</span><span class="media-btn plus">+</span><span class="media-btn minus">−</span></div><p class="product-text">Nemo nisi ipsum quas illo dolores ut voluptatem</p><div class="price">$ 543.00 <svg width="20" height="18" viewBox="0 0 18 16"><path d="M1 1h3l2 9h9l2-7H5" fill="none" stroke="#d71f26" stroke-width="1.6"/><circle cx="7" cy="14" r="1.4" fill="#d71f26"/><circle cx="14" cy="14" r="1.4" fill="#d71f26"/></svg></div><a class="btn-more" href="#">read more</a></article>
    <article class="product-card"><div class="product-media" style="--a:#d2a27a;--b:#6e3f2a" role="img" aria-label="Product photo of a person in warm light"><span class="stars">★★★★★</span><span class="media-btn plus">+</span><span class="media-btn minus">−</span></div><p class="product-text">Nemo nisi ipsum quas illo dolores ut voluptatem</p><div class="price">$ 543.00 <svg width="20" height="18" viewBox="0 0 18 16"><path d="M1 1h3l2 9h9l2-7H5" fill="none" stroke="#d71f26" stroke-width="1.6"/><circle cx="7" cy="14" r="1.4" fill="#d71f26"/><circle cx="14" cy="14" r="1.4" fill="#d71f26"/></svg></div><a class="btn-more" href="#">read more</a></article>
  </div>
</section>

<!-- as featured in -->
<section class="section" style="margin-top:24px">
  <div class="section-head"><span class="section-title">as featured in</span><span class="arrow-btn">‹</span><span class="arrow-btn">›</span></div>
</section>
<div class="partners">
  <span class="partner-name">Brenfield</span>
  <span class="partner-name">Velquist</span>
  <span class="partner-name">Pinemark</span>
  <span class="partner-name">Ostrel</span>
  <span class="partner-name">Quillby</span>
</div>

<aside class="ebook-banner">
  <div class="ebook-art" role="img" aria-label="Book cover illustration for a mathematics lecture series"></div>
  <div class="ebook-copy">You have access to this eBook series<br>through your library!</div>
  <div class="ebook-publisher">Spreeling Press</div>
</aside>

<div class="quote-band">
  <span>"I have never met a designer who was not eager to keep things the same as they were" - <b>Arlo Penwick</b> http://kipdorra.com/q/Pn8 #KIPDORRA</span>
</div>

<footer class="site-footer">
  <div><h4>BUY or BROWSE</h4><ul><li>Boats</li><li>Cars</li><li>Electronics</li><li>Real Estate</li><li>Roommates</li><li>Video</li><li>Read More</li></ul></div>
  <div><h4>ADRESS</h4><ul><li>18 Harbor Lane</li><li>Suite 4 Westfield</li><li>Portland OR</li><li>Business Hours</li><li>Mon - Fri</li></ul></div>
  <div><h4>SELL</h4><ul><li>Start Selling</li><li>Seller Guide</li><li>Upcoming Trades</li><li>Featured Sales</li><li>Selling Fees</li></ul></div>
  <div><h4>GOOD AT FUN?</h4><div class="footer-map" role="img" aria-label="Map of the service region"></div></div>
  <div><h4>STAY UPDATE WITH US</h4>
    <div class="subscribe"><span>enter email address</span><b></b></div>
    <div class="pay-cards"><span></span><span></span><span></span><span></span></div>
    <div class="socials"><span></span><span></span><span></span><span></span><span></span></div>
  </div>
</footer>
<div class="bottom-bar"><span>© 2013 Kip Dorra</span><nav><span>About us</span><span>Blog</span><span>Terms of use</span><span>Privacy Policy</span><span>Search</span><span>Contact us</span></nav></div>

</div>
</body>
</html>
```